VELKO Website Redesign in Wix

Task:
Create a new design for all pages of the VELKO technology website in Wix. Specifications are:
Color palette preferences: black, white, gray, purple, blue. See VELKO Ref Doc provided.
Please refer to the VELKO_ref doc for a sample of the desired color palette
Typesetting must be in Montserrat
Brand will be that of a Marketing Technology company
Looking for vibrant, highly engaging images and organized, digestible flow. Open to suggestions
Required format is Wix.
VELKO logo does NOT need to be redesigned. Please use the files provided for the VELKO logo.
Look and feel
Each slider illustrates characteristics of the customer's brand and the style your logo design should communicate.

```html
<!DOCTYPE html>
<html lang="en">
<head>
<meta charset="utf-8">
<title>VELKO – Self-service content delivery</title>
<link rel="stylesheet" href="https://fonts.googleapis.com/css2?family=Montserrat:wght@400;500;600;700&display=swap">
<style>
:root{
  --purple-deep:#3a14b8;
  --purple:#5a23c8;
  --purple-bright:#6a1fd0;
  --violet:#8a3cc8;
  --lilac:#a77cf0;
  --ink:#2b2b33;
  --body:#444450;
  --mist:#eef0f4;
  --cell:#f2f2f6;
  --white:#ffffff;
  --tick:#3cb371;
  --cross:#e0203a;
  --orange:#ff8a00;
  --footer:#1c1c22;
}
*{box-sizing:border-box;margin:0;padding:0}
html,body{width:1200px;height:4677px;overflow:hidden}
body{font-family:'Montserrat',sans-serif;color:var(--ink);background:var(--white);position:relative}
/* nav */
.site-nav{position:absolute;top:0;left:0;width:1200px;height:80px;background:var(--purple-deep)}
.brand{position:absolute;left:0;top:0;width:283px;height:80px;background:#e6e6e6;display:flex;align-items:center;justify-content:center;font-size:46px;font-weight:500;letter-spacing:8px;color:#111}
.nav-link{position:absolute;top:29px;transform:translateX(-50%);font-size:15px;font-weight:600;color:var(--white);white-space:nowrap}
.nav-link.active{color:var(--lilac)}
/* hero */
.hero{position:absolute;top:80px;left:0;width:1200px;height:704px;background:radial-gradient(ellipse at 70% 30%,#7a2ee0 0%,var(--purple-bright) 30%,var(--purple-deep) 75%,#2a0f9a 100%);color:var(--white);text-align:center}
.hero-title{position:absolute;top:150px;width:100%;font-size:128px;font-weight:700;letter-spacing:2px}
.hero-title sup{font-size:70px;vertical-align:top;position:relative;top:14px}
.hero-sub{position:absolute;top:300px;width:100%;font-size:33px;font-weight:600;line-height:42px}
.btn-primary{position:absolute;left:497px;top:468px;width:206px;height:53px;background:var(--violet);color:var(--white);font-size:23px;font-weight:600;display:flex;align-items:center;justify-content:center}
.slider-dots{position:absolute;left:1129px;top:312px}
.slider-dots span{display:block;width:10px;height:10px;border-radius:50%;background:#8d5ad8;margin-bottom:13px}
.slider-dots span:first-child{background:var(--white)}
/* features */
.feature{position:absolute;top:880px;width:336px;text-align:center;transform:translateX(-50%)}
.feature svg{display:block;margin:0 auto 22px}
.feature h3{font-size:24px;font-weight:700;color:var(--purple);line-height:34px}
.feature p{margin-top:18px;font-size:14px;line-height:27.5px;color:var(--body)}
/* how */
.how{position:absolute;top:1316px;left:0;width:1200px;height:1526px;background:var(--mist)}
.section-title{position:absolute;width:100%;text-align:center;font-size:44px;font-weight:700}
.how-intro{position:absolute;top:150px;left:100px;width:1000px;text-align:center;font-size:16px;line-height:31px;color:var(--ink)}
.illus{position:absolute;border-radius:40px}
.step{position:absolute}
.step h3{font-size:34px;font-weight:700;color:var(--purple);margin-bottom:14px}
.step p{font-size:18px;line-height:35px;color:var(--ink);width:560px}
.step a{display:inline-block;margin-top:26px;font-size:18px;font-weight:500;color:var(--purple);text-decoration:none}
/* compare */
.compare{position:absolute;top:2842px;left:0;width:1200px;height:609px;background:linear-gradient(120deg,var(--purple-deep),#4a14c0 50%,#2e10a8)}
.compare .section-title{top:65px;color:var(--white);font-size:44px}
.table{position:absolute;left:76px;top:155px;width:1050px;display:grid;grid-template-columns:184px repeat(6,1fr);gap:3px}
.th{height:73px;background:#1e9be0;color:var(--white);display:flex;flex-direction:column;align-items:center;justify-content:center;font-size:21px;font-weight:500}
.th svg{margin-bottom:2px}
.th.first{background:#2aa3e6}
.rl{height:46px;background:var(--cell);font-size:12px;font-weight:600;line-height:13px;display:flex;align-items:center;justify-content:center;text-align:center;color:#333}
.cell{height:46px;background:var(--cell);display:flex;align-items:center;justify-content:center}
/* awards */
.awards{position:absolute;top:3451px;left:0;width:1200px;height:440px;background:#f7f7f9}
.awards .section-title{top:60px;font-size:40px}
.award{position:absolute;top:170px;width:230px;transform:translateX(-50%);text-align:center;font-size:18px;line-height:24px;color:#333}
.award .badge{margin:0 auto 10px;background:#d9dbe4}
.award.small{font-size:15px;line-height:22px}
/* contact */
.contact{position:absolute;top:3891px;left:0;width:1200px;height:640px;background:linear-gradient(135deg,#4a1ca8,#6a2ec8 50%,#3c1690)}
.contact .section-title{top:50px;color:var(--white);font-size:40px}
.field{position:absolute;background:var(--white);font-size:15px;color:#333;padding:11px 14px}
.submit{position:absolute;left:163px;top:406px;width:874px;height:53px;background:var(--orange);color:var(--white);font-size:22px;font-weight:600;display:flex;align-items:center;justify-content:center}
.contact-line{position:absolute;top:494px;width:100%;text-align:center;color:var(--white);font-size:25px;font-weight:600;display:flex;justify-content:center;align-items:center;gap:14px}
/* footer */
.site-footer{position:absolute;top:4531px;left:0;width:1200px;height:146px;background:var(--footer);color:var(--white);text-align:center}
.copyright{position:absolute;top:43px;width:100%;font-size:13px}
.social{position:absolute;top:76px;width:100%;display:flex;justify-content:center;gap:22px}
.social span{width:22px;height:22px;border-radius:50%;background:var(--white)}
</style>
</head>
<body>
<svg width="0" height="0" style="position:absolute">
  <defs>
    <symbol id="tick" viewBox="0 0 32 32"><path d="M5 17l7 7L27 8" fill="none" stroke="#3cb371" stroke-width="5" stroke-linecap="round" stroke-linejoin="round"/></symbol>
    <symbol id="cross" viewBox="0 0 32 32"><path d="M7 7l18 18M25 7L7 25" fill="none" stroke="#e0203a" stroke-width="5" stroke-linecap="round"/></symbol>
  </defs>
</svg>

<header class="site-nav">
  <div class="brand">VELKO</div>
  <span class="nav-link active" style="left:379px">Home</span>
  <span class="nav-link" style="left:506px">How it works</span>
  <span class="nav-link" style="left:690px">VELKO Applications</span>
  <span class="nav-link" style="left:855px">Company</span>
  <span class="nav-link" style="left:989px">Contact Us</span>
  <span class="nav-link" style="left:1102px">More</span>
</header>

<section class="hero" role="img" aria-label="Purple gradient backdrop with a faint network of connected lines">
  <h1 class="hero-title">VELKO<sup>™</sup></h1>
  <p class="hero-sub">Increase and perfect your connection &nbsp;with consumers<br>using VELKO™'s &nbsp;patented self-service content<br>delivery technology</p>
  <div class="btn-primary">Learn More</div>
  <div class="slider-dots"><span></span><span></span><span></span><span></span></div>
</section>

<section class="features">
  <div class="feature" style="left:238px">
    <svg width="86" height="86" viewBox="0 0 86 86" role="img" aria-label="Platform icon"><rect x="6" y="8" width="74" height="56" rx="4" fill="none" stroke="#5a23c8" stroke-width="3"/><circle cx="34" cy="36" r="13" fill="none" stroke="#5a23c8" stroke-width="3"/><rect x="56" y="40" width="24" height="38" rx="3" fill="none" stroke="#5a23c8" stroke-width="3"/></svg>
    <h3>Our Revolutionary<br>Platform</h3>
    <p>Whether you're marketing software, selling a product, or looking to close a deal – find out your target market and quickly modify your campaigns to reach consumers silently and securely.</p>
  </div>
  <div class="feature" style="left:601px">
    <svg width="86" height="86" viewBox="0 0 86 86" role="img" aria-label="Strategy icon"><rect x="6" y="8" width="66" height="56" rx="4" fill="none" stroke="#5a23c8" stroke-width="3"/><circle cx="52" cy="52" r="15" fill="none" stroke="#5a23c8" stroke-width="3"/><path d="M63 63l16 16" stroke="#5a23c8" stroke-width="4"/><path d="M16 50V38M26 50V28M36 50V34" stroke="#5a23c8" stroke-width="3"/></svg>
    <h3>Strategy Towards Market<br>Dominance</h3>
    <p>Whether you're marketing software, selling a product, or looking to close a deal – find out your target market and quickly modify your campaigns to reach consumers silently and securely.</p>
  </div>
  <div class="feature" style="left:962px">
    <svg width="86" height="86" viewBox="0 0 86 86" role="img" aria-label="Innovation icon"><circle cx="40" cy="36" r="20" fill="none" stroke="#5a23c8" stroke-width="3"/><rect x="32" y="58" width="16" height="16" rx="2" fill="none" stroke="#5a23c8" stroke-width="3"/><circle cx="62" cy="22" r="9" fill="none" stroke="#5a23c8" stroke-width="3"/></svg>
    <h3>Proven Success in<br>Innovation</h3>
    <p>Whether you're marketing software, selling a product, or looking to close a deal – find out your target market and quickly modify your campaigns to reach consumers silently and securely.</p>
  </div>
</section>

<section class="how">
  <h2 class="section-title" style="top:75px">How it works</h2>
  <p class="how-intro">Our platform delivers individualized content that immediately increases engagement over any communication medium using VELKO's patented data packets.</p>

  <div class="illus" role="img" aria-label="Illustration of a person at a desk creating content across several screens" style="left:40px;top:287px;width:454px;height:309px;background:linear-gradient(135deg,#f3e3c6,#5aa6e0 60%,#2f3b8a)"></div>
  <div class="step" style="left:525px;top:355px">
    <h3>Content Creation</h3>
    <p>Self service content creation allows businesses to easily create and execute any campaign.</p>
    <a>Learn More &nbsp;›</a>
  </div>

  <div class="step" style="left:75px;top:760px">
    <h3>Compliance and Security</h3>
    <p>Multi-layered solutions meeting identity verification, privacy and data sovereignty regulations.</p>
    <a>Learn More &nbsp;›</a>
  </div>
  <div class="illus" role="img" aria-label="Illustration of a secure browser window with a shield and padlock beside a person" style="left:690px;top:672px;width:445px;height:354px;background:linear-gradient(135deg,#d8ccf4,#8a6ee0 55%,#4a3aa8)"></div>

  <div class="illus" role="img" aria-label="Illustration of two people opting in to content on a large app screen" style="left:54px;top:1117px;width:458px;height:278px;background:linear-gradient(135deg,#c9c6f0,#eef0fa 50%,#8d8ae0)"></div>
  <div class="step" style="left:537px;top:1165px">
    <h3>Consumer App</h3>
    <p>Consumers have the opportunity to knowingly Opt in to interact with content.</p>
    <a>Learn More &nbsp;›</a>
  </div>
</section>

<section class="compare">
  <h2 class="section-title">Current Technology vs VELKO™</h2>
  <div class="table">
    <div class="th first">Features</div>
    <div class="th"><svg width="30" height="24" viewBox="0 0 30 24"><path d="M3 8v8M8 4v16M13 1v22M18 4v16M23 7v10M27 10v4" stroke="#fff" stroke-width="2.5"/></svg>VELKO</div>
    <div class="th"><svg width="30" height="24" viewBox="0 0 30 24"><path d="M3 9a17 17 0 0 1 24 0M8 14a10 10 0 0 1 14 0" fill="none" stroke="#fff" stroke-width="3"/><circle cx="15" cy="19" r="2.5" fill="#fff"/></svg>WLAN</div>
    <div class="th"><svg width="30" height="24" viewBox="0 0 30 24"><circle cx="15" cy="12" r="4" fill="#fff"/><circle cx="15" cy="12" r="9" fill="none" stroke="#fff" stroke-width="2"/></svg>Pairing</div>
    <div class="th"><svg width="30" height="24" viewBox="0 0 30 24"><circle cx="15" cy="9" r="3" fill="#fff"/><path d="M15 12v10M8 3a10 10 0 0 0 0 12M22 3a10 10 0 0 1 0 12" fill="none" stroke="#fff" stroke-width="2.5"/></svg>RFID</div>
    <div class="th"><svg width="30" height="24" viewBox="0 0 30 24"><path d="M9 6a8 8 0 0 1 0 12M15 3a13 13 0 0 1 0 18" fill="none" stroke="#fff" stroke-width="2.5"/></svg>NFC</div>
    <div class="th"><svg width="30" height="24" viewBox="0 0 30 24"><circle cx="15" cy="7" r="4" fill="#fff"/><circle cx="6" cy="17" r="4" fill="#fff"/><circle cx="24" cy="17" r="4" fill="#fff"/></svg>Social</div>

    <div class="rl">operates without<br>a network</div>
    <div class="cell"><svg width="30" height="30"><use href="#tick"/></svg></div><div class="cell"><svg width="26" height="26"><use href="#cross"/></svg></div><div class="cell"><svg width="26" height="26"><use href="#cross"/></svg></div><div class="cell"><svg width="26" height="26"><use href="#cross"/></svg></div><div class="cell"><svg width="26" height="26"><use href="#cross"/></svg></div><div class="cell"><svg width="26" height="26"><use href="#cross"/></svg></div>

    <div class="rl">operates without<br>live power</div>
    <div class="cell"><svg width="30" height="30"><use href="#tick"/></svg></div><div class="cell"><svg width="26" height="26"><use href="#cross"/></svg></div><div class="cell"><svg width="26" height="26"><use href="#cross"/></svg></div><div class="cell"><svg width="26" height="26"><use href="#cross"/></svg></div><div class="cell"><svg width="26" height="26"><use href="#cross"/></svg></div><div class="cell"><svg width="26" height="26"><use href="#cross"/></svg></div>

    <div class="rl">transmits data<br>securely</div>
    <div class="cell"><svg width="30" height="30"><use href="#tick"/></svg></div><div class="cell"><svg width="30" height="30"><use href="#tick"/></svg></div><div class="cell"><svg width="30" height="30"><use href="#tick"/></svg></div><div class="cell"><svg width="30" height="30"><use href="#tick"/></svg></div><div class="cell"><svg width="30" height="30"><use href="#tick"/></svg></div><div class="cell"><svg width="26" height="26"><use href="#cross"/></svg></div>

    <div class="rl">private</div>
    <div class="cell"><svg width="30" height="30"><use href="#tick"/></svg></div><div class="cell"><svg width="30" height="30"><use href="#tick"/></svg></div><div class="cell"><svg width="30" height="30"><use href="#tick"/></svg></div><div class="cell"><svg width="30" height="30"><use href="#tick"/></svg></div><div class="cell"><svg width="30" height="30"><use href="#tick"/></svg></div><div class="cell"><svg width="26" height="26"><use href="#cross"/></svg></div>

    <div class="rl">customization</div>
    <div class="cell"><svg width="30" height="30"><use href="#tick"/></svg></div><div class="cell"><svg width="30" height="30"><use href="#tick"/></svg></div><div class="cell"><svg width="30" height="30"><use href="#tick"/></svg></div><div class="cell"><svg width="30" height="30"><use href="#tick"/></svg></div><div class="cell"><svg width="30" height="30"><use href="#tick"/></svg></div><div class="cell"><svg width="30" height="30"><use href="#tick"/></svg></div>

    <div class="rl">carried by audio<br>soundwaves</div>
    <div class="cell"><svg width="30" height="30"><use href="#tick"/></svg></div><div class="cell"><svg width="26" height="26"><use href="#cross"/></svg></div><div class="cell"><svg width="26" height="26"><use href="#cross"/></svg></div><div class="cell"><svg width="26" height="26"><use href="#cross"/></svg></div><div class="cell"><svg width="26" height="26"><use href="#cross"/></svg></div><div class="cell"><svg width="26" height="26"><use href="#cross"/></svg></div>
  </div>
</section>

<section class="awards">
  <h2 class="section-title">Awards</h2>
  <div class="award small" style="left:182px">
    <div class="badge" style="width:74px;height:74px;border-radius:6px"></div>
    Northfield Founders Circle 1998 Coastal Region Finalist
  </div>
  <div class="award small" style="left:454px">
    <div class="badge" style="width:74px;height:74px;border-radius:50%"></div>
    Beacon Awards – Gold Winner, Lifestyle Impact
  </div>
  <div class="award" style="left:730px;top:200px">
    <div class="badge" style="width:150px;height:44px;border-radius:4px"></div>
    Market Ledger<br>30 under 30
  </div>
  <div class="award" style="left:1004px;top:206px">
    <div class="badge" style="width:150px;height:44px;border-radius:4px"></div>
    Market Ledger<br>40 under 40
  </div>
</section>

<section class="contact" role="img" aria-label="Photo of a team at work under a purple overlay">
  <h2 class="section-title">What Can We Help You With?</h2>
  <div class="field" style="left:163px;top:134px;width:422px;height:44px">Name</div>
  <div class="field" style="left:615px;top:134px;width:422px;height:44px">Email Address</div>
  <div class="field" style="left:163px;top:199px;width:874px;height:45px">Subject</div>
  <div class="field" style="left:163px;top:264px;width:874px;height:128px">Message</div>
  <div class="submit">Submit</div>
  <div class="contact-line">
    <svg width="26" height="20" viewBox="0 0 26 20"><rect x="1" y="1" width="24" height="18" rx="2" fill="#fff"/><path d="M2 3l11 8 11-8" fill="none" stroke="#5a23c8" stroke-width="2"/></svg>
    <span>info@velkotech.com &nbsp;| </span>
    <svg width="22" height="22" viewBox="0 0 22 22"><path d="M5 2l4 4-2 3c1 3 3 5 6 6l3-2 4 4-3 3C9 20 2 13 2 5z" fill="#fff"/></svg>
    <span>1-866-TRY-VELKO</span>
  </div>
</section>

<footer class="site-footer">
  <p class="copyright">Copyright © 2022 Company Name All Right Reserved</p>
  <div class="social" aria-label="Social media links"><span></span><span></span><span></span><span></span><span></span></div>
</footer>
</body>
</html>
```